Harborline Renewal Business Card Design

Professional and clean design. The design colors should flow with the logo. Two-sided card with the website on the back which is:

www.HarborlineRenewal.example.

"Specializing in Water Damage Restoration"

On the front I need the name, email, phone, and logo.

Name: Darnell Quisby
Email: Darnell@HarborlineRenewal.example
Phone: 555-318-2046 for now

I only have the Preview and Thumbnail right now but should have the source files uploaded within a day or two.

Target Market(s)

Flood victims, home owners with water damage from busted pipes etc...

Industry/Entity Type

Business

Contact Information for Business Card

Name: Darnell Quisby

Font styles to use
Serif
Sans Serif

Requirements
Must have
• Business Card Details Info

```html
<!DOCTYPE html>
<html lang="en">
<head>
<meta charset="UTF-8">
<title>Harborline Renewal Business Card</title>
<link rel="stylesheet" href="https://fonts.googleapis.com/css2?family=Open+Sans:wght@400;600;700&display=swap">
<style>
  :root {
    --stage: #2b2b2d;
    --card-black: #030303;
    --brand-blue: #2a9ad8;
    --light-blue: #4fc0ef;
    --white: #ffffff;
  }
  * { margin: 0; padding: 0; box-sizing: border-box; }
  html, body { width: 1200px; height: 900px; overflow: hidden; background: var(--stage); }
  .canvas {
    width: 1200px; height: 900px;
    display: flex; flex-direction: column; align-items: center; justify-content: center; gap: 40px;
    font-family: "Open Sans", Arial, sans-serif;
  }
  .card {
    position: relative; width: 640px; height: 366px;
    background: var(--card-black); border-radius: 18px; overflow: hidden;
  }
  /* Back side */
  .card-back .brand-block {
    position: absolute; top: 62px; left: 0; right: 0;
    display: flex; align-items: center; justify-content: center; gap: 16px;
  }
  .brand-dot { width: 54px; height: 54px; border-radius: 50%; background: var(--brand-blue); flex: none; }
  .brand-name {
    color: var(--brand-blue); font-weight: 600; letter-spacing: 2px; text-transform: uppercase;
  }
  .card-back .brand-name { font-size: 30px; }
  .card-back .tagline {
    position: absolute; top: 218px; left: 0; right: 0; text-align: center;
    color: var(--brand-blue); font-size: 15px; letter-spacing: 0.5px;
  }
  .card-back .web-rule {
    position: absolute; top: 244px; left: 40px; right: 40px;
    display: flex; align-items: center; gap: 10px;
    color: var(--brand-blue); font-size: 14px;
  }
  .web-rule .rule { flex: 1; height: 1px; background: var(--brand-blue); }
  .card-back .edge-line {
    position: absolute; bottom: 14px; left: 0; right: 0; height: 2px; background: var(--brand-blue);
  }
  /* Front side */
  .card-front .wave { position: absolute; inset: 0; width: 100%; height: 100%; }
  .card-front .brand-block {
    position: absolute; left: 44px; top: 100px;
    display: flex; align-items: center; gap: 14px;
  }
  .card-front .brand-name { font-size: 24px; line-height: 1.25; }
  .contact {
    position: absolute; right: 26px; top: 158px; text-align: right; color: var(--white);
  }
  .contact .person { font-size: 22px; font-weight: 700; letter-spacing: 1px; text-transform: uppercase; margin-bottom: 10px; }
  .contact .line { display: flex; justify-content: flex-end; align-items: center; gap: 7px; font-size: 13px; line-height: 20px; }
  .contact svg { width: 11px; height: 11px; flex: none; }
</style>
</head>
<body>
<main class="canvas">
  <section class="card card-back">
    <div class="brand-block">
      <span class="brand-dot"></span>
      <span class="brand-name">Harborline Renewal</span>
    </div>
    <p class="tagline">SPECIALIZING IN WATER DAMAGE RESTORATION</p>
    <div class="web-rule"><span class="rule"></span><span>www.HarborlineRenewal.example</span><span class="rule"></span></div>
    <div class="edge-line"></div>
  </section>

  <section class="card card-front">
    <svg class="wave" viewBox="0 0 640 366" preserveAspectRatio="none">
      <path d="M150 366 C240 350 280 300 310 222 C350 128 420 92 640 86 L640 366 Z" fill="var(--light-blue)"/>
      <path d="M160 366 C252 352 292 302 321 226 C361 133 425 100 640 94 L640 366 Z" fill="var(--white)"/>
      <path d="M170 366 C260 350 300 300 330 230 C370 140 430 110 640 100 L640 366 Z" fill="var(--brand-blue)"/>
    </svg>
    <div class="brand-block">
      <span class="brand-dot"></span>
      <span class="brand-name">Harborline<br>Renewal</span>
    </div>
    <div class="contact">
      <p class="person">Darnell Quisby</p>
      <p class="line">555-318-2046
        <svg viewBox="0 0 12 12"><path d="M2.5 1 L4.5 1 L5.2 3.5 L4 4.5 C4.7 6 6 7.3 7.5 8 L8.5 6.8 L11 7.5 L11 9.5 C11 10.3 10.3 11 9.5 11 C5 11 1 7 1 2.5 C1 1.7 1.7 1 2.5 1 Z" fill="var(--white)"/></svg>
      </p>
      <p class="line">Darnell@HarborlineRenewal.example
        <svg viewBox="0 0 12 12"><rect x="1" y="2.5" width="10" height="7" rx="1" fill="none" stroke="var(--white)"/><path d="M1 3 L6 7 L11 3" fill="none" stroke="var(--white)"/></svg>
      </p>
      <p class="line">www.HarborlineRenewal.example
        <svg viewBox="0 0 12 12"><circle cx="6" cy="6" r="5" fill="none" stroke="var(--white)"/><path d="M1 6 H11 M6 1 C3.5 3.5 3.5 8.5 6 11 M6 1 C8.5 3.5 8.5 8.5 6 11" fill="none" stroke="var(--white)" stroke-width="0.8"/></svg>
      </p>
    </div>
  </section>
</main>
</body>
</html>
```